RTavenor Business Cards & Letterhead

I have a logo but need a design for some new business cards. We are a Design-Build Firm that specializes in the design and construction of commercial projects.
the cards need to be professional. no cartoon stuff.
i would like to have the cards in AI format so I can update the card as needed. Logo is provided.
Our Address is: 4187 Marlowe Ct. Apex, North Carolina 27614

```html
<!DOCTYPE html>
<html lang="en">
<head>
<meta charset="utf-8">
<title>RTavenor Business Card</title>
<link href="https://fonts.googleapis.com/css2?family=Arimo:wght@400;700&display=swap" rel="stylesheet">
<style>
  :root {
    --backdrop: #3a3a3a;
    --paper: #f5f5f6;
    --ink: #4a4a4a;
    --ink-soft: #707070;
    --brand: #0a67a6;
    --brand-deep: #005484;
    --brand-light: #0b78bb;
    --rule: #b9b9b9;
  }
  html, body {
    margin: 0;
    width: 1200px;
    height: 1200px;
    overflow: hidden;
    background: var(--backdrop);
    font-family: "Arimo", Arial, sans-serif;
  }
  .card {
    position: absolute;
    width: 686px;
    height: 390px;
    left: 258px;
    box-sizing: border-box;
  }
  .card-front {
    top: 174px;
    background: var(--paper);
    border-bottom-left-radius: 92px;
    color: var(--ink);
  }
  .card-back {
    top: 640px;
    background: radial-gradient(ellipse at 50% 50%, var(--brand-light) 0%, var(--brand) 45%, var(--brand-deep) 100%);
    border-bottom-right-radius: 92px;
  }
  .wordmark {
    position: absolute;
    left: 77px;
    top: 178px;
    display: flex;
    align-items: center;
    gap: 10px;
    font-weight: 700;
    font-size: 34px;
    letter-spacing: 0.5px;
    color: var(--ink);
    line-height: 1;
  }
  .wordmark-square {
    width: 26px;
    height: 26px;
    background: var(--brand);
  }
  .divider {
    position: absolute;
    left: 364px;
    top: 105px;
    width: 1px;
    height: 184px;
    background: var(--rule);
  }
  .details {
    position: absolute;
    left: 385px;
    top: 103px;
  }
  .person-name {
    margin: 0;
    font-size: 22px;
    font-weight: 700;
    color: var(--brand);
    line-height: 26px;
  }
  .person-title {
    margin: 0 0 10px;
    font-size: 15px;
    color: var(--ink-soft);
    line-height: 18px;
  }
  .address {
    margin: 0 0 8px;
    font-size: 16px;
    line-height: 20px;
    font-style: normal;
  }
  .contacts {
    list-style: none;
    margin: 0;
    padding: 0;
    font-size: 16px;
    line-height: 20.5px;
  }
  .contacts li {
    display: flex;
    align-items: center;
    gap: 10px;
  }
  .contacts svg {
    width: 15px;
    height: 15px;
    fill: var(--brand);
    flex: none;
  }
  .back-mark {
    position: absolute;
    left: 240px;
    top: 92px;
    width: 206px;
    height: 206px;
    border-radius: 14px;
    background: linear-gradient(160deg, var(--brand-light), var(--brand-deep));
    box-shadow: 0 0 0 1px rgba(255,255,255,0.12) inset;
  }
</style>
</head>
<body>
  <section class="card card-front">
    <div class="wordmark"><span class="wordmark-square"></span>RTAVENOR</div>
    <div class="divider"></div>
    <div class="details">
      <h1 class="person-name">Daniel Hollis</h1>
      <p class="person-title">Managing Director</p>
      <address class="address">4187 Marlowe Ct. Apex<br>North Carolina 27614</address>
      <ul class="contacts">
        <li><svg viewBox="0 0 16 16"><path d="M3.5 1l2.5 3-1.5 2c.8 1.8 2.2 3.2 4 4l2-1.5 3 2.5-1.5 2.5C7 14.5 1.5 9 1 2.5z"/></svg>919-555-0142</li>
        <li><svg viewBox="0 0 16 16"><path d="M4 1h8v14H4zM5.5 2.5v9h5v-9zM7.2 12.5h1.6v1.2H7.2z" fill-rule="evenodd"/></svg>919-555-0187</li>
        <li><svg viewBox="0 0 16 16"><path d="M1 4h14v9H1zM2.5 5.2V12h11V5.2L8 9.2z"/></svg>info@rtavenor.com</li>
        <li><svg viewBox="0 0 16 16"><circle cx="8" cy="8" r="7"/><path d="M5 4c1 1 2 1 2 2.5S5 8 4.5 9.5M10 3c0 1.5 1.5 2 3 2.5M9 12.5c0-1.5 1-2.5 2.5-2.5" stroke="#f5f5f6" stroke-width="1.2" fill="none"/></svg>www.rtavenor.com</li>
      </ul>
    </div>
  </section>
  <section class="card card-back">
    <div class="back-mark" aria-hidden="true"></div>
  </section>
</body>
</html>
```